New Brand - Website Design (4 Pages)

We are launching a new brand for electronic cigarettes. We already have logo and packaging done and would like a web design to go with it.

We are interested in the following deliverables:

1) Home Page Design
2) Check Out Design
3) How it Works Page
4) Secondary Template Page Design

Looking for a 60s modern look and something that is consistent with our logo and packaging.

Industry/Entity Type

Electronic

Requirements
Must have
• Consistent with logo and packaging (Use Logo Attached)
White background

Example (Functionality & Design): http://www.moltrafen.co.uk/
Example (Design): http://www.brendolark.com/

We want the design more like brendolark but the functionality the same as moltrafen.

Top Bar: Pale Dunes Kits; Cartridge Refills; How it Works; Contact; My Account; Checkout
Should not have
• Stock List or Search Bar or Newsletter Signup

```html
<!DOCTYPE html>
<html lang="en">
<head>
<meta charset="utf-8">
<title>Pale Dunes — How it Works</title>
<link rel="stylesheet" href="https://fonts.googleapis.com/css2?family=Quicksand:wght@300;400;500;600&display=swap">
<style>
  :root {
    --sky: #8dd5f6;
    --ink: #111111;
    --night: #000000;
    --paper: #ffffff;
    --stone: #b3b3b3;
    --heading-grey: #b9b9b9;
    --line: #7f8c93;
    --icon-blue: #6fc6ee;
  }
  * { box-sizing: border-box; margin: 0; padding: 0; }
  html, body { width: 1141px; height: 1200px; overflow: hidden; }
  body {
    position: relative;
    font-family: "Quicksand", sans-serif;
    color: var(--ink);
    background:
      repeating-linear-gradient(90deg, rgba(0,0,0,0.025) 0 2px, transparent 2px 5px),
      linear-gradient(180deg, #e9e9e9 0%, #f4f4f4 60%, #ffffff 100%);
  }

  .page {
    position: absolute;
    left: 68px; top: 36px;
    width: 996px; height: 1126px;
    background: var(--paper);
    box-shadow: 0 0 8px rgba(0,0,0,0.35);
  }

  /* Header */
  .site-header {
    position: absolute; left: 0; top: 0;
    width: 100%; height: 188px;
    background: linear-gradient(180deg, #ffffff 0%, #f6f6f6 70%, #eeeeee 100%);
  }
  .brand-name {
    position: absolute; left: 0; top: 72px; width: 100%;
    text-align: center;
    font-size: 50px; font-weight: 500; letter-spacing: 6px; line-height: 1;
    color: var(--ink);
  }

  /* Navigation */
  .main-nav {
    position: absolute; left: 0; top: 248px;
    width: 1141px; height: 42px;
    background: var(--paper);
    border: 1px solid #c9c9c9;
    box-shadow: 0 2px 4px rgba(0,0,0,0.25);
    display: flex; align-items: center; justify-content: center;
    font-size: 18px; letter-spacing: 1px; color: #333;
  }
  .main-nav a { color: inherit; text-decoration: none; }
  .main-nav .sep { margin: 0 6px; }

  /* Blue band */
  .promo-band {
    position: absolute; left: 0; top: 275px;
    width: 100%; height: 122px;
    background: var(--sky);
  }
  .promo-link {
    position: absolute; top: 0; height: 100%;
    display: flex; align-items: center; justify-content: center;
    font-size: 17px; font-weight: 600; letter-spacing: 2px; color: var(--ink);
  }
  .promo-link.how { left: 0; width: 220px; }
  .promo-link.checkout { left: 220px; width: 227px; }
  .promo-divider {
    position: absolute; top: 18px; height: 84px;
    border-left: 1px dashed rgba(255,255,255,0.9);
  }
  .promo-divider.one { left: 220px; }
  .promo-divider.two { left: 447px; }
  .promo-text {
    position: absolute; left: 476px; top: 18px; width: 496px;
    font-size: 12.4px; line-height: 1.22; color: var(--ink);
  }

  /* How it works */
  .how-section { position: absolute; left: 0; top: 397px; width: 100%; height: 425px; }
  .section-title {
    position: absolute; right: 56px; top: 20px;
    font-size: 33px; font-weight: 300; letter-spacing: 1px;
    color: var(--heading-grey);
  }
  .steps { position: absolute; left: 0; top: 108px; width: 100%; height: 60px; }
  .step {
    position: absolute; top: 0; width: 58px; height: 58px; border-radius: 50%;
    background: var(--stone); color: var(--paper);
    display: flex; align-items: center; justify-content: center;
    font-size: 42px; font-weight: 400;
  }
  .step-dot {
    position: absolute; top: 25px; width: 8px; height: 8px; border-radius: 50%;
    background: var(--stone);
  }
  .how-text {
    position: absolute; left: 118px; top: 222px; width: 760px;
    text-align: center; font-size: 15.4px; line-height: 1.3; color: var(--ink);
  }

  /* Flavors */
  .flavors {
    position: absolute; left: 0; top: 826px;
    width: 100%; height: 300px;
    background: var(--night);
    border-top: 2px solid #d8d8d8;
    color: var(--paper);
  }
  .flavors-title {
    position: absolute; left: 0; top: 20px; width: 100%;
    text-align: center; font-size: 31px; font-weight: 500; letter-spacing: 4px;
  }
  .flavors-rule { position: absolute; top: 41px; height: 1px; background: var(--line); }
  .flavors-rule.left { left: 18px; width: 372px; }
  .flavors-rule.right { left: 604px; width: 374px; }
  .flavor { position: absolute; top: 112px; width: 190px; text-align: center; }
  .flavor-icon {
    width: 74px; height: 74px; margin: 0 auto;
    border-radius: 10px;
    background: linear-gradient(135deg, #1b3f52 0%, #2b6b8a 100%);
    border: 1px solid var(--icon-blue);
  }
  .flavor-name { margin-top: 18px; font-size: 17px; letter-spacing: 1.5px; color: #e8e8e8; }
  .flavor-dot {
    position: absolute; top: 198px; width: 15px; height: 15px; border-radius: 50%;
    background: var(--paper);
  }

  /* Footer */
  .site-footer {
    position: absolute; left: 0; top: 1174px; width: 1141px;
    text-align: center; font-size: 13px; color: #333;
  }
</style>
</head>
<body>

<div class="page">
  <header class="site-header">
    <div class="brand-name">PALE DUNES</div>
  </header>

  <section class="promo-band">
    <div class="promo-link how">HOW IT WORKS</div>
    <div class="promo-divider one"></div>
    <div class="promo-link checkout">CHECK OUT</div>
    <div class="promo-divider two"></div>
    <p class="promo-text">Lorem ipsum dolor sit amet, consectetuer adipiscing elit, sed diam nonummy nibh euismod tincidunt ut laoreet dolore magna aliquam erat volutpat. Ut wisi enim ad minim veniam, quis nostrud exerci tation ullamcorper suscipit lobortis nisl ut aliquip ex ea commodo consequat.</p>
  </section>

  <section class="how-section">
    <h2 class="section-title">HOW IT WORKS</h2>
    <div class="steps">
      <div class="step" style="left:267px">1</div>
      <span class="step-dot" style="left:331px"></span><span class="step-dot" style="left:343px"></span>
      <div class="step" style="left:363px">2</div>
      <span class="step-dot" style="left:426px"></span><span class="step-dot" style="left:438px"></span>
      <div class="step" style="left:457px">3</div>
      <span class="step-dot" style="left:521px"></span><span class="step-dot" style="left:533px"></span>
      <div class="step" style="left:552px">4</div>
      <span class="step-dot" style="left:619px"></span><span class="step-dot" style="left:631px"></span>
      <div class="step" style="left:652px">5</div>
    </div>
    <p class="how-text">Lorem ipsum dolor sit amet, consectetuer adipiscing elit, sed diam nonummy nibh euismod tincidunt ut laoreet dolore magna aliquam erat volutpat. Ut wisi enim ad minim veniam, quis nostrud exerci tation ullamcorper suscipit lobortis nisl ut aliquip ex ea commodo consequat. Duis autem vel eum iriure dolor in hendrerit in vulputate velit esse molestie consequat,</p>
  </section>

  <section class="flavors">
    <span class="flavors-rule left"></span>
    <h2 class="flavors-title">FLAVORS</h2>
    <span class="flavors-rule right"></span>

    <div class="flavor" style="left:47px">
      <div class="flavor-icon" role="img" aria-label="Line illustration of a tobacco leaf"></div>
      <div class="flavor-name">Tobacco Classic</div>
    </div>
    <span class="flavor-dot" style="left:248px"></span>
    <div class="flavor" style="left:244px">
      <div class="flavor-icon" role="img" aria-label="Line illustration of mint leaves"></div>
      <div class="flavor-name">Menthol</div>
    </div>
    <span class="flavor-dot" style="left:403px"></span>
    <div class="flavor" style="left:414px">
      <div class="flavor-icon" role="img" aria-label="Line illustration of a peeled banana"></div>
      <div class="flavor-name">Banana</div>
    </div>
    <span class="flavor-dot" style="left:583px"></span>
    <div class="flavor" style="left:593px">
      <div class="flavor-icon" role="img" aria-label="Line illustration of an apple"></div>
      <div class="flavor-name">Apple</div>
    </div>
    <span class="flavor-dot" style="left:761px"></span>
    <div class="flavor" style="left:785px">
      <div class="flavor-icon" role="img" aria-label="Line illustration of a thumbs-up in a circle"></div>
      <div class="flavor-name">Non-Nicotine</div>
    </div>
  </section>
</div>

<nav class="main-nav">
  <a href="#">Home</a><span class="sep">|</span>
  <a href="#">Pale Dunes Kits</a><span class="sep">|</span>
  <a href="#">Cartridge Refills</a><span class="sep">|</span>
  <a href="#">How it Works</a><span class="sep">|</span>
  <a href="#">Contact</a><span class="sep">|</span>
  <a href="#">My Account</a><span class="sep">|</span>
  <a href="#">Checkout</a>
</nav>

<footer class="site-footer">Copyright 2013 PaleDunes - Terms &amp; Conditions | Privacy Policy</footer>

</body>
</html>
```